Real Estate Business Card

On the front side I want to have my info, my brokerage info.
On the back side I want have my complany’s logo, website and Facebook link. I will provide all this once I select a design.

I would like to see Black background and gold text, Dark Blue and gold text and White and blue text designs

Font styles to use
Sans Serif
Script

```html
<!DOCTYPE html>
<html lang="en">
<head>
<meta charset="utf-8">
<title>Harborline Real Estate – Business Card</title>
<link rel="stylesheet" href="https://fonts.googleapis.com/css2?family=Montserrat:wght@700;800&family=Roboto:wght@400;500;700&display=swap">
<style>
  :root {
    --backdrop: #2b2b2d;
    --card: #1f1f21;
    --card-edge: #2c2c2f;
    --gold: #f2cf5b;
    --red: #e23a40;
    --slate: #6a7285;
    --text: #ffffff;
    --muted: #9aa0ad;
  }
  * { box-sizing: border-box; margin: 0; padding: 0; }
  html, body {
    width: 1200px; height: 900px; overflow: hidden;
    background: var(--backdrop);
    font-family: "Roboto", Arial, sans-serif;
  }
  .canvas { position: relative; width: 1200px; height: 900px; }
  .card {
    position: absolute; left: 170px; width: 860px; height: 390px;
    background: var(--card);
    border: 1px solid var(--card-edge);
    box-shadow: 0 18px 40px rgba(0,0,0,.45);
    overflow: hidden;
  }
  .card--back { top: 40px; }
  .card--front { top: 470px; }

  .brand-name {
    font-family: "Montserrat", Arial, sans-serif;
    font-weight: 800;
    color: var(--slate);
    text-transform: uppercase;
    letter-spacing: 1px;
    line-height: 1.1;
    text-align: center;
  }
  .card--back .brand-name {
    position: absolute; left: 0; right: 0; top: 150px;
    font-size: 46px;
  }
  .card--front .brand-name {
    position: absolute; left: 40px; width: 400px; top: 140px;
    font-size: 36px;
  }

  .divider {
    position: absolute; left: 470px; top: 50px; width: 2px; height: 220px;
    background: linear-gradient(to bottom, transparent, #d0d0d0 50%, transparent);
  }

  .contact { position: absolute; left: 510px; top: 60px; color: var(--text); }
  .contact__name {
    font-family: "Montserrat", Arial, sans-serif; font-weight: 800;
    font-size: 30px; color: var(--gold); letter-spacing: .5px;
  }
  .contact__role {
    font-size: 20px; font-weight: 500; color: var(--red);
    margin-top: -2px; margin-bottom: 18px;
  }
  .contact__address { font-size: 20px; line-height: 1.25; margin-bottom: 14px; }
  .contact__row { display: flex; align-items: center; gap: 10px; font-size: 20px; line-height: 1.35; }
  .contact__icon { width: 20px; height: 20px; flex: none; }

  .footer-bands { position: absolute; left: 0; bottom: 0; width: 860px; height: 70px; }
  .website {
    position: absolute; right: 40px; bottom: 12px;
    font-size: 22px; font-weight: 500; color: var(--text);
    letter-spacing: 7px;
  }
</style>
</head>
<body>
<main class="canvas">

  <section class="card card--back" aria-label="Card back">
    <p class="brand-name">Harborline Real Estate</p>
  </section>

  <section class="card card--front" aria-label="Card front">
    <p class="brand-name">Harborline<br>Real Estate</p>

    <div class="divider"></div>

    <div class="contact">
      <p class="contact__name">DANA WHITFIELD</p>
      <p class="contact__role">CEO/FOUNDER</p>
      <p class="contact__address">2140 Willow Crest Drive<br>Fairbanks, Alaska 99701</p>
      <p class="contact__row">
        <svg class="contact__icon" viewBox="0 0 24 24" aria-hidden="true"><path fill="var(--gold)" d="M6.6 10.8a15.1 15.1 0 0 0 6.6 6.6l2.2-2.2c.3-.3.7-.4 1-.2 1.1.4 2.3.6 3.6.6.6 0 1 .4 1 1V20c0 .6-.4 1-1 1A17 17 0 0 1 3 4c0-.6.4-1 1-1h3.5c.6 0 1 .4 1 1 0 1.3.2 2.5.6 3.6.1.3 0 .7-.2 1z"/></svg>
        555 214 7390
      </p>
      <p class="contact__row">
        <svg class="contact__icon" viewBox="0 0 24 24" aria-hidden="true"><rect x="2" y="5" width="20" height="14" rx="1" fill="var(--gold)"/><path d="M3 6l9 7 9-7" fill="none" stroke="var(--card)" stroke-width="1.8"/></svg>
        dana@harborline.com
      </p>
      <p class="contact__row">
        <svg class="contact__icon" viewBox="0 0 24 24" aria-hidden="true"><circle cx="12" cy="12" r="10" fill="var(--gold)"/></svg>
        /harborline
      </p>
    </div>

    <svg class="footer-bands" viewBox="0 0 860 70" preserveAspectRatio="none" aria-hidden="true">
      <polygon points="0,20 480,34 470,46 0,34" fill="var(--slate)"/>
      <polygon points="480,24 860,40 860,70 440,70" fill="var(--red)"/>
    </svg>
    <p class="website">www.harborline.com</p>
  </section>

</main>
</body>
</html>
```